Corporate Travel Technology Company needs new Business Card design

We need a new business card design to reflect our re-branded company. Our company is called Tolven (pronounced tolvenn) and we provide Business Intelligence and Corporate Journey Platform solutions for the corporate travel industry. Our multinational customers use our solutions to manage large travel budgets and frequent travellers, as well as to save money and reduce risk. We'd like to see designs that use the blue and green palette as well as our corporate logo (attached below). The design should communicate innovation, insight, forward thinking, contemporary, trusted.

Target Market(s)

Large multinational corporates and Travel Agencies.

Industry/Entity Type

Business

Contact Information for Business Card

Rosalind Mercer
Chief Executive
Tolven
Phone number - +61 (0)2 8134 2907
Email address - rosalind.mercer@tolven-example.com
Mobile number - +61 (0)438 516 702
www.tolven-example.com

Font styles to use
Other font styles liked:
• Please use font as close to corporate logo as possible

Colors
0255a3
0393ce
00a990
33b8a4
33a6d7
3176b5

Requirements
Must have
• Please include the words;
• Corporate Journey Platform
• Clearer Data for Every Business Trip
• Use corporate logo - although icon can be stylised if needed

```html
<!DOCTYPE html>
<html lang="en">
<head>
<meta charset="utf-8">
<title>Tolven business card</title>
<link rel="stylesheet" href="https://fonts.googleapis.com/css2?family=Open+Sans:wght@400;600;700&display=swap">
<style>
  :root {
    --bg: #d9dadb;
    --card: #ffffff;
    --slate: #445f5c;
    --blue: #29a8e0;
    --white: #ffffff;
  }
  * { box-sizing: border-box; margin: 0; padding: 0; }
  html, body { width: 1200px; height: 900px; overflow: hidden; }
  body {
    background: var(--bg);
    font-family: "Open Sans", Arial, sans-serif;
    position: relative;
  }
  .card {
    position: absolute;
    left: 290px;
    width: 620px;
    height: 354px;
    background: var(--card);
    box-shadow: 0 4px 14px rgba(0,0,0,0.18);
    overflow: hidden;
  }
  .card--front { top: 60px; }
  .card--back { top: 478px; }

  .brand {
    color: var(--slate);
    font-weight: 600;
    letter-spacing: 1px;
    line-height: 1;
    white-space: nowrap;
  }
  .card--front .brand {
    position: absolute;
    top: 76px;
    left: 0;
    right: 0;
    text-align: center;
    font-size: 80px;
  }
  .tagline {
    position: absolute;
    left: 0;
    right: 0;
    text-align: center;
    white-space: nowrap;
  }
  .tagline--service {
    top: 214px;
    color: var(--blue);
    font-size: 19px;
    font-weight: 600;
  }
  .tagline--promise {
    top: 246px;
    color: var(--slate);
    font-size: 21px;
    font-weight: 700;
  }

  .card__art { position: absolute; inset: 0; }
  .card--back .brand {
    position: absolute;
    top: 46px;
    left: 40px;
    font-size: 56px;
  }
  .person {
    position: absolute;
    top: 46px;
    right: 36px;
    text-align: right;
    color: var(--white);
  }
  .person__name { font-size: 19px; font-weight: 700; }
  .person__role { font-size: 14px; font-weight: 400; margin-top: 2px; }
  .contacts {
    position: absolute;
    right: 30px;
    bottom: 40px;
    list-style: none;
    color: var(--white);
    font-size: 15px;
    line-height: 24px;
    text-align: right;
  }
  .contacts li { display: flex; justify-content: flex-end; align-items: center; gap: 9px; white-space: nowrap; }
  .contacts svg { width: 13px; height: 13px; flex: none; }
</style>
</head>
<body>

  <section class="card card--front">
    <p class="brand">Tolven</p>
    <p class="tagline tagline--service">Corporate Journey Platform</p>
    <p class="tagline tagline--promise">Clearer Data for Every Business Trip</p>
  </section>

  <section class="card card--back">
    <svg class="card__art" viewBox="0 0 620 354" width="620" height="354" aria-hidden="true">
      <path d="M150 354 C 250 300, 320 190, 372 0 L620 0 L620 354 Z" fill="var(--slate)"/>
      <path d="M112 354 C 215 300, 285 210, 330 108" fill="none" stroke="var(--blue)" stroke-width="16"/>
      <polygon points="308,110 352,112 336,72" fill="var(--blue)"/>
    </svg>

    <p class="brand">Tolven</p>

    <div class="person">
      <p class="person__name">Rosalind Mercer</p>
      <p class="person__role">Chief Executive</p>
    </div>

    <ul class="contacts">
      <li>+61 (0)2 8134 2907
        <svg viewBox="0 0 14 14"><path d="M1 5 Q7 1 13 5 L11 7 L9 5.5 L5 5.5 L3 7 Z M3 8 H11 V12 H3 Z" fill="var(--white)"/></svg>
      </li>
      <li>+61 (0)438 516 702
        <svg viewBox="0 0 14 14"><rect x="3.5" y="1" width="7" height="12" rx="1.5" fill="var(--white)"/><rect x="5" y="3" width="4" height="6" fill="var(--slate)"/></svg>
      </li>
      <li>rosalind.mercer@tolven-example.com
        <svg viewBox="0 0 14 14"><rect x="1" y="3" width="12" height="8" fill="var(--white)"/><path d="M1 3 L7 8 L13 3" fill="none" stroke="var(--slate)" stroke-width="1.2"/></svg>
      </li>
      <li>www.tolven-example.com
        <svg viewBox="0 0 14 14"><g fill="none" stroke="var(--white)" stroke-width="1.6"><rect x="1.5" y="6" width="6" height="4" rx="2" transform="rotate(-45 4.5 8)"/><rect x="6.5" y="4" width="6" height="4" rx="2" transform="rotate(-45 9.5 6)"/></g></svg>
      </li>
    </ul>
  </section>

</body>
</html>
```